brightwell - Property Management DL Card

I am after a savvy designer to cut through junk mail! so many real estate agents use flyers to promote themselves and their business and usually sales. We are a property management firm (residential) and we want to represent landlords that have existing investment properties and need a quality agent to represent them. Can you help?
DL size, will be printed and delivered to mailboxes. For a look at our website go to www.brightwellrs.com.au. Keep it simple and clutter free.
it is to be double sided - with one side to be simple and clear - just our website, logo and telephone number on the back.
attached is our logo and our telephone number is 1300 48 92 16
the above are 2 essential elements to be included + our email address: admin@brightwellrs.com.au
also attached are our transparent price list

Target Market(s)
property investors,
people that manage properties themselves
Industry/Entity Type
Property Management
- arial
Look and feel

```html
<!DOCTYPE html>
<html lang="en">
<head>
<meta charset="utf-8">
<title>brightwell – Property Management DL Card</title>
<link rel="stylesheet" href="https://fonts.googleapis.com/css2?family=Open+Sans:wght@300;400;600;700&display=swap">
<style>
  :root {
    --page-bg: #e4e4e4;
    --frame-taupe: #c4bfb3;
    --card-taupe: #b1aa9a;
    --panel-white: #ffffff;
    --ink: #2a2a2a;
    --ink-soft: #333333;
    --contact-ink: #3f372d;
    --bullet-grey: #9a9a9a;
    --band-green: #5cb43c;
    --band-green-light: #a9d98e;
    --photo-light: #e9ebe6;
    --photo-mid: #b8b4a6;
    --photo-green: #7fa85a;
    --photo-floor: #4a4a48;
    --logo-band: #111111;
  }
  * { box-sizing: border-box; margin: 0; padding: 0; }
  html, body { width: 1200px; height: 1200px; overflow: hidden; }
  body {
    background: var(--page-bg);
    font-family: "Open Sans", Arial, sans-serif;
    position: relative;
  }

  /* Front side */
  .card-front {
    position: absolute; left: 118px; top: 55px;
    width: 1003px; height: 500px;
    background: var(--frame-taupe);
  }
  .front-photo {
    position: absolute; left: 23px; top: 23px;
    width: 647px; height: 455px;
    background:
      linear-gradient(180deg, rgba(255,255,255,0) 60%, var(--photo-floor) 100%),
      linear-gradient(90deg, var(--photo-green) 0%, var(--photo-light) 35%, var(--photo-light) 70%, var(--photo-mid) 100%);
  }
  .front-panel {
    position: absolute; left: 670px; top: 23px;
    width: 310px; height: 455px;
    background: var(--panel-white);
  }
  .headline-band {
    position: absolute; left: 442px; top: 116px;
    width: 530px; height: 28px;
    background: linear-gradient(90deg, rgba(92,180,60,0) 0%, var(--band-green) 22%, var(--band-green) 75%, var(--band-green-light) 100%);
  }
  .headline {
    position: absolute; left: 548px; top: 116px;
    line-height: 28px;
    color: #fff; font-weight: 600; font-size: 20px;
    white-space: nowrap;
  }
  .benefits {
    position: absolute; left: 700px; top: 156px;
    list-style: none;
    font-size: 16.5px; color: var(--ink-soft);
    line-height: 21.7px;
  }
  .benefits li { position: relative; padding-left: 15px; }
  .benefits li::before {
    content: ""; position: absolute; left: 1px; top: 7px;
    width: 7px; height: 7px; background: var(--bullet-grey);
    transform: rotate(45deg);
  }
  .front-brand {
    position: absolute; left: 750px; top: 388px;
    font-weight: 300; font-size: 40px; color: var(--ink);
    letter-spacing: -0.5px; line-height: 1;
  }

  /* Back side */
  .card-back {
    position: absolute; left: 121px; top: 638px;
    width: 1001px; height: 500px;
    background: var(--card-taupe);
  }
  .back-brand-band {
    position: absolute; left: 34px; top: 51px;
    width: 365px; height: 69px;
    background: linear-gradient(90deg, rgba(17,17,17,0) 0%, var(--logo-band) 18%, var(--logo-band) 70%, rgba(17,17,17,0) 100%);
  }
  .back-brand {
    position: absolute; left: 134px; top: 60px;
    font-weight: 300; font-size: 36px; color: #fff;
    letter-spacing: -0.5px; line-height: 1.3;
  }
  .contact {
    position: absolute; left: 555px; top: 377px;
    border-left: 2px solid var(--contact-ink);
    padding-left: 19px;
    color: var(--contact-ink);
    font-size: 18px; line-height: 24px; letter-spacing: 0.5px;
  }
  .contact .call-label { font-size: 17px; margin-right: 8px; }
  .contact .phone { font-weight: 700; font-size: 22px; letter-spacing: 1px; }
</style>
</head>
<body>
  <section class="card-front" aria-label="Card front">
    <div class="front-photo" role="img" aria-label="Photo of a bright, modern living room with sofa, glass coffee table, potted palm and garden view"></div>
    <div class="front-panel"></div>
    <div class="headline-band"></div>
    <h1 class="headline">Property Management specialists</h1>
    <ul class="benefits">
      <li>Excellent communication</li>
      <li>No hidden extras</li>
      <li>Minimal vacancy</li>
      <li>The best rent return</li>
    </ul>
    <div class="front-brand">brightwell</div>
  </section>

  <section class="card-back" aria-label="Card back">
    <div class="back-brand-band"></div>
    <div class="back-brand">brightwell</div>
    <address class="contact" style="font-style:normal">
      <div><span class="call-label">CALL TODAY!</span> <span class="phone">1300 48 92 16</span></div>
      <div>PO Box B302, Sydney South NSW, 1235</div>
      <div>admin@brightwellrs.com.au</div>
    </address>
  </section>
</body>
</html>
```